International business needs business cards

Our company, DRV Ventures Inc. is in the business of supplying a range construction products with particular emphasis on CEMENT. We have developed our own brand - TORVAN SUPPLIES - with which to infiltrate the market. We are launching our brand of cement (TORVAN Type IS Cement) into the Caribbean which is unlike anything this market has ever seen. A monopoly has existed here for the past 60-odd years and the market has now opened to allow the importation of other brands and consumers are anxious and ready for change/improvement. We are very excited to be launching and want to make a great first impression. We will be conducting workshops and seminars (from government level to the hardware store owners) and we want our business card to give us the strong, confident introduction that we need.

Target Market(s)

construction; builders; engineers; home owners

Industry/Entity Type

Construction

Contact Information for Business Card

Marisol Depree
CEO
cell # 1 555 4180736
Ground floor,Lindell Plaza Suite 2734
George Town,Grand Cayman
Cayman Islands,KY1-4823
EMAIL: m.depree@drvventuresinc.example
web site drvventuresinc.example

COMPANY: skype info drv.ventures.example

second card
Yvette Brannock-Depree
CFO
CELL# 1 555 607 3941
George Town,Grand Cayman
Cayman Islands,KY1-4823
EMAIL: y.brannockdepree@drvventuresinc.example
website drvventuresinc.example

Requirements
Must have
• Business cards must display BOTH logos - DRV is the company and TORVAN is the brand.

```html
<!DOCTYPE html>
<html lang="en">
<head>
<meta charset="utf-8">
<title>DRV Ventures Inc. — Business Card</title>
<link rel="stylesheet" href="https://fonts.googleapis.com/css2?family=Open+Sans:wght@400;600;700&display=swap">
<style>
  :root {
    --bg: #e9e6e1;
    --card-black: #0d0d0d;
    --card-black-hi: #262626;
    --card-white: #ffffff;
    --brand-red: #8e1b1b;
    --name-red: #9a1c1c;
    --ink: #1a1a1a;
    --text-grey: #5b5b5b;
    --rule-grey: #d6d6d6;
    --web-grey: #c9c9c9;
  }
  * { box-sizing: border-box; margin: 0; padding: 0; }
  html, body { width: 1200px; height: 950px; overflow: hidden; }
  body {
    background: var(--bg);
    font-family: "Open Sans", Arial, sans-serif;
    position: relative;
  }
  .card {
    position: absolute;
    left: 240px;
    width: 720px;
    height: 410px;
    border-radius: 4px;
    box-shadow: 0 6px 18px rgba(0,0,0,.18);
    overflow: hidden;
  }
  /* Front */
  .card--front {
    top: 45px;
    background: linear-gradient(160deg, var(--card-black-hi) 0%, var(--card-black) 55%);
    display: flex;
    flex-direction: column;
    align-items: center;
    justify-content: center;
  }
  .front-mark {
    display: flex;
    align-items: center;
    gap: 18px;
  }
  .front-mark__square {
    width: 120px;
    height: 120px;
    background: var(--brand-red);
  }
  .front-mark__name {
    color: #ffffff;
    font-weight: 700;
    font-size: 30px;
  }
  .front-web {
    margin-top: 46px;
    color: var(--web-grey);
    font-size: 17px;
    letter-spacing: 4px;
  }
  /* Back */
  .card--back {
    top: 495px;
    background: var(--card-white);
  }
  .back-logos {
    position: absolute;
    left: 0;
    top: 0;
    width: 340px;
    height: 360px;
    display: flex;
    flex-direction: column;
    align-items: center;
    justify-content: center;
    gap: 38px;
  }
  .company-logo {
    display: flex;
    align-items: center;
    gap: 12px;
  }
  .company-logo__square {
    width: 64px;
    height: 64px;
    background: var(--brand-red);
  }
  .company-logo__name {
    font-weight: 700;
    font-size: 26px;
    color: var(--ink);
  }
  .brand-logo {
    display: flex;
    align-items: center;
    gap: 10px;
  }
  .brand-logo__circle {
    width: 54px;
    height: 54px;
    border-radius: 50%;
    background: #7a7a7a;
  }
  .brand-logo__name {
    font-weight: 700;
    font-size: 20px;
    color: #4a4a4a;
    letter-spacing: 1px;
  }
  .back-divider {
    position: absolute;
    left: 340px;
    top: 40px;
    width: 1px;
    height: 285px;
    background: var(--rule-grey);
  }
  .contact {
    position: absolute;
    left: 370px;
    top: 50px;
    color: var(--text-grey);
  }
  .contact__name {
    color: var(--name-red);
    font-size: 26px;
    font-weight: 600;
    line-height: 1.1;
  }
  .contact__role {
    color: var(--ink);
    font-size: 16px;
    margin-bottom: 18px;
  }
  .contact__address {
    font-style: normal;
    font-size: 17px;
    line-height: 1.4;
    margin-bottom: 12px;
  }
  .contact__list { list-style: none; font-size: 16px; line-height: 1.65; }
  .contact__list li { display: flex; align-items: center; gap: 8px; }
  .contact__list svg { width: 15px; height: 15px; flex: none; }
  .back-band {
    position: absolute;
    left: 0;
    right: 0;
    bottom: 0;
    height: 38px;
    background: var(--brand-red);
    border-top: 6px solid #ffffff;
    box-shadow: 0 -2px 0 var(--brand-red);
  }
</style>
</head>
<body>

<section class="card card--front" aria-label="Business card front">
  <div class="front-mark">
    <div class="front-mark__square"></div>
    <span class="front-mark__name">DRV Ventures Inc.</span>
  </div>
  <p class="front-web">www.drvventuresinc.example</p>
</section>

<section class="card card--back" aria-label="Business card back">
  <div class="back-logos">
    <div class="company-logo">
      <div class="company-logo__square"></div>
      <span class="company-logo__name">DRV Ventures Inc.</span>
    </div>
    <div class="brand-logo">
      <div class="brand-logo__circle"></div>
      <span class="brand-logo__name">TORVAN SUPPLIES</span>
    </div>
  </div>

  <div class="back-divider"></div>

  <div class="contact">
    <h1 class="contact__name">Marisol Depree</h1>
    <p class="contact__role">CEO</p>
    <address class="contact__address">
      Ground floor<br>
      Lindell Plaza Suite 2734<br>
      George Town,Grand Cayman<br>
      Cayman Islands,KY1-4823
    </address>
    <ul class="contact__list">
      <li>
        <svg viewBox="0 0 16 16" aria-hidden="true"><rect x="3.5" y="1" width="9" height="14" rx="1.5" fill="none" stroke="#8e1b1b" stroke-width="2"/></svg>
        1 555 4180736
      </li>
      <li>
        <svg viewBox="0 0 16 16" aria-hidden="true"><rect x="1" y="3" width="14" height="10" fill="#8e1b1b"/><path d="M1 3l7 6 7-6" fill="none" stroke="#fff" stroke-width="1.3"/></svg>
        m.depree@drvventuresinc.example
      </li>
      <li>
        <svg viewBox="0 0 16 16" aria-hidden="true"><circle cx="8" cy="8" r="7" fill="#8e1b1b"/><path d="M1 8h14M8 1c-3 3.5-3 10.5 0 14M8 1c3 3.5 3 10.5 0 14" fill="none" stroke="#fff" stroke-width="1"/></svg>
        drvventuresinc.example
      </li>
    </ul>
  </div>

  <div class="back-band"></div>
</section>

</body>
</html>
```